New Start Up Website for Volt Roam Mobile - Mobile EV Charging

I need an informational website built to support my new start up. Should be clean and very straight forward. Home, About, Vehicles we Support, Links to iOS and Android apps, Contact Us. Volt Roam Mobile is an emergency / express EV charging solution. Charging as a Service as the industry is being dubbed. I believe I am second to market next to Quill Amp and their Flowlet mobile solution.
Updates

Website must be built on Wordpress!

Target Market(s)

EV Owners

Industry/Entity Type

EV Charging

Coding

Coded - Design and coding required

Number of Pages Required

4 page

Font styles to use
Sans Serif

Colors
59FF00
82FF00
B8FF75
E3FFCB
F4FFEA

Requirements
Must have
• I will not have any real pics for at least 60 days. I will need place holders or a mock up of the vehicle.
Nice to have
• Quillamp.io is our competitor. They own Flowlet APP which is what we're modeling.

```html
<!DOCTYPE html>
<html lang="en">
<head>
<meta charset="utf-8">
<title>Volt Roam Mobile – Home and About pages</title>
<link rel="stylesheet" href="https://fonts.googleapis.com/css2?family=Montserrat:wght@400;500;600;700;800;900&display=swap">
<style>
  :root {
    --board: #dedede;
    --label: #3a3a3a;
    --page: #ffffff;
    --ink: #1d1d1d;
    --navy: #0b1a6b;
    --footer: #03124a;
    --blue: #0a3cff;
    --blue-active: #1a5cff;
    --periwinkle: #aab5fb;
    --volt: #59ff00;
    --white: #ffffff;
  }
  * { margin: 0; padding: 0; box-sizing: border-box; }
  html, body { width: 1200px; height: 782px; overflow: hidden; }
  body {
    background: var(--board);
    font-family: "Montserrat", Arial, sans-serif;
    color: var(--ink);
    position: relative;
  }
  .board-label {
    position: absolute; top: 24px;
    font-size: 24px; font-weight: 400; color: var(--label);
    transform: translateX(-50%);
  }
  .page {
    position: absolute; background: var(--page); overflow: hidden;
    box-shadow: 3px 3px 4px rgba(0,0,0,.28);
  }
  .page--home { left: 69px; top: 64px; width: 572px; height: 662px; }
  .page--about { left: 722px; top: 64px; width: 405px; height: 656px; }

  /* header */
  .site-header { position: absolute; left: 0; top: 0; width: 100%; }
  .brand { position: absolute; display: flex; align-items: center; gap: 3px; font-weight: 700; color: var(--navy); white-space: nowrap; }
  .brand-dot { border-radius: 50%; background: var(--volt); }
  .nav { position: absolute; }
  .nav a { position: absolute; white-space: nowrap; color: var(--ink); text-decoration: none; transform: translateY(-50%); }
  .nav a.is-active { color: var(--blue-active); }
  .btn-pill {
    position: absolute; display: flex; align-items: center; justify-content: center;
    border-radius: 999px; background: var(--blue); color: var(--white); white-space: nowrap;
  }

  /* hero */
  .hero-bg { position: absolute; left: 0; }
  .hero-title { position: absolute; color: var(--white); white-space: nowrap; line-height: 1; }

  /* home hero */
  .home-hero-bg { top: 49px; width: 572px; height: 290px; }
  .welcome { left: 53px; top: 102px; font-size: 51px; font-weight: 900; letter-spacing: -0.5px; }
  .welcome-sub { left: 53px; top: 152px; font-size: 25px; font-weight: 400; }
  .hero-copy { position: absolute; left: 57px; top: 181px; width: 225px; font-size: 7.4px; line-height: 9.5px; color: var(--white); }
  .btn-hero {
    position: absolute; top: 224px; width: 91px; height: 15.5px; border-radius: 999px;
    display: flex; align-items: center; justify-content: center; font-size: 8px; font-weight: 500; color: var(--white);
  }
  .btn-hero--solid { left: 53px; background: var(--blue); }
  .btn-hero--outline { left: 156px; border: 1.3px solid var(--white); }

  .section-title { position: absolute; left: 0; width: 100%; text-align: center; font-weight: 800; color: var(--navy); transform: translateY(-50%); }
  .features-title { top: 361px; font-size: 16.5px; }

  .feature-card {
    position: absolute; top: 409px; width: 136px; height: 146px; border-radius: 15px;
    display: flex; align-items: center; justify-content: center; text-align: center;
    color: var(--white); font-size: 12.5px; font-weight: 700; line-height: 15px; padding-bottom: 30px;
  }
  .feature-card--about { left: 55px; background: linear-gradient(180deg, #3a3f55 0%, #2d3a78 45%, #1d3596 80%); }
  .feature-card--vehicles { left: 219px; background: linear-gradient(180deg, #7d8497 0%, #1d6a8e 35%, #1f4aa0 65%, #1c3596 85%); }
  .feature-card--apps { left: 381px; background: linear-gradient(180deg, #b9bfcc 0%, #7f8fbd 35%, #3a56b0 65%, #1c3596 85%); }

  /* footer */
  .site-footer { position: absolute; left: 0; width: 100%; background: var(--footer); }
  .footer-nav a { position: absolute; color: var(--white); text-decoration: none; white-space: nowrap; transform: translateY(-50%); }
  .email-field {
    position: absolute; background: var(--white); border-radius: 999px; display: flex; align-items: center;
    color: #9a9a9a; font-style: italic;
  }
  .copyright { position: absolute; font-weight: 600; color: var(--ink); white-space: nowrap; transform: translateY(-50%); }
  .social { position: absolute; display: flex; }
  .social span { border-radius: 50%; background: var(--ink); }

  /* home header + footer sizes */
  .page--home .brand { left: 53px; top: 19px; font-size: 8px; }
  .page--home .brand-dot { width: 9px; height: 9px; }
  .page--home .nav a { top: 25px; font-size: 6px; }
  .page--home .login { left: 473px; top: 18px; width: 46px; height: 13px; font-size: 4.5px; }
  .page--home .site-footer { top: 596px; height: 44px; }
  .page--home .footer-nav a { top: 22px; font-size: 6px; }
  .page--home .email-field { left: 341px; top: 15px; width: 126px; height: 13px; font-size: 5px; padding-left: 7px; }
  .page--home .subscribe { left: 473px; top: 15px; width: 46px; height: 13px; font-size: 4.6px; }
  .page--home .copyright { left: 53px; top: 652px; font-size: 5px; }
  .page--home .social { left: 461px; top: 648px; gap: 6px; }
  .page--home .social span { width: 6px; height: 6px; }

  /* about page */
  .page--about .brand { left: 38px; top: 13px; font-size: 6px; }
  .page--about .brand-dot { width: 7px; height: 7px; }
  .page--about .nav a { top: 17.5px; font-size: 4.4px; }
  .page--about .login { left: 335px; top: 13px; width: 32px; height: 9px; font-size: 3.4px; }
  .about-hero-bg { top: 35px; width: 405px; height: 205px; }
  .about-title { left: 0; width: 100%; text-align: center; top: 103px; font-size: 38px; font-weight: 900; }
  .about-lede { position: absolute; left: 80px; top: 139px; width: 245px; text-align: center; font-size: 5px; line-height: 6.5px; color: var(--white); }
  .who-title { top: 256px; font-size: 12px; }
  .who-copy { position: absolute; left: 49px; top: 278px; width: 307px; text-align: center; font-size: 4px; line-height: 6.9px; color: #333; }
  .page--about .read-more { left: 186px; top: 388px; width: 33px; height: 9px; font-size: 2.8px; }
  .team-band { position: absolute; left: 0; top: 426px; width: 100%; height: 184px; background: var(--periwinkle); }
  .team-title { top: 34px; font-size: 12px; }
  .team-card {
    position: absolute; top: 51px; width: 96px; height: 104px; border-radius: 10px;
    display: flex; flex-direction: column; align-items: center; justify-content: flex-end; padding-bottom: 27px; color: var(--white);
  }
  .team-card--first { left: 39px; background: linear-gradient(180deg, #8a8fa3 0%, #4d5a8c 45%, #2a45a8 75%, #1c3596 100%); }
  .team-card--second { left: 155px; background: linear-gradient(180deg, #e6e2e6 0%, #d9d4d8 55%, #c4c9d4 100%); }
  .team-card--third { left: 269px; background: linear-gradient(180deg, #fafafa 0%, #f1f1f1 55%, #e3e8ee 100%); }
  .member-name { font-size: 9px; font-weight: 700; }
  .member-links { display: flex; gap: 4px; margin-top: 3px; }
  .member-links span { width: 5px; height: 5px; border-radius: 50%; background: var(--white); }
  .page--about .site-footer { top: 610px; height: 31px; }
  .page--about .footer-nav a { top: 15px; font-size: 4.2px; }
  .page--about .email-field { left: 241px; top: 11px; width: 90px; height: 9px; font-size: 3.4px; padding-left: 5px; }
  .page--about .subscribe { left: 336px; top: 11px; width: 31px; height: 9px; font-size: 3.2px; }
  .page--about .copyright { left: 38px; top: 648px; font-size: 3.6px; }
  .page--about .social { left: 327px; top: 646px; gap: 4px; }
  .page--about .social span { width: 4.5px; height: 4.5px; }
</style>
</head>
<body>

<div class="board-label" style="left:334px">Home</div>
<div class="board-label" style="left:922px">About</div>

<!-- Home page -->
<section class="page page--home">
  <header class="site-header">
    <div class="brand"><span class="brand-dot"></span>Volt Roam Mobile</div>
    <nav class="nav">
      <a class="is-active" style="left:190px">Home</a>
      <a style="left:222px">About</a>
      <a style="left:254px">Vehicles we support</a>
      <a style="left:329px">Link to IOS and Android Apps</a>
      <a style="left:428px">Contact us</a>
    </nav>
    <span class="btn-pill login">LOGIN</span>
  </header>

  <svg class="hero-bg home-hero-bg" viewBox="0 0 572 290" role="img" aria-label="Photo of a white charging van driving along a beach at sunset under a blue overlay">
    <defs>
      <linearGradient id="homeHeroFill" x1="0" y1="0" x2="1" y2="1">
        <stop offset="0" stop-color="#2a46b8"/>
        <stop offset="0.45" stop-color="#3d55a8"/>
        <stop offset="0.72" stop-color="#5b5f98"/>
        <stop offset="1" stop-color="#b97a64"/>
      </linearGradient>
    </defs>
    <polygon points="0,0 572,0 572,290 0,219" fill="url(#homeHeroFill)"/>
  </svg>
  <h1 class="hero-title welcome">Welcome</h1>
  <p class="hero-title welcome-sub">To Our Website</p>
  <p class="hero-copy">Lorem ipsum dolor sit amet, consectetuer adipiscing elit, sed diam nonummy nibh euismod tincidunt ut laoreet dolore magna aliquam erat vol</p>
  <a class="btn-hero btn-hero--solid">More Detail</a>
  <a class="btn-hero btn-hero--outline">View Demo</a>

  <h2 class="section-title features-title">Features</h2>
  <div class="feature-card feature-card--about" role="img" aria-label="Team meeting photo card: About">About</div>
  <div class="feature-card feature-card--vehicles" role="img" aria-label="Vehicle paperwork photo card: Vehicles we Support">Vehicles we<br>Support</div>
  <div class="feature-card feature-card--apps" role="img" aria-label="Phone and app icons photo card: Links to iOS and Android apps">Links to<br>iOS and Android<br>apps</div>

  <footer class="site-footer">
    <nav class="footer-nav">
      <a style="left:53px">Home</a>
      <a style="left:85px">About</a>
      <a style="left:119px">Vehicles we support</a>
      <a style="left:192px">Link to IOS and Android Apps</a>
      <a style="left:291px">Contact us</a>
    </nav>
    <span class="email-field">E-Mail Address</span>
    <span class="btn-pill subscribe">Subscribe</span>
  </footer>
  <p class="copyright">Copyright © 2020 Volt Roam Mobile</p>
  <div class="social" aria-label="Social links"><span></span><span></span><span></span><span></span><span></span></div>
</section>

<!-- About page -->
<section class="page page--about">
  <header class="site-header">
    <div class="brand"><span class="brand-dot"></span>Volt Roam Mobile</div>
    <nav class="nav">
      <a style="left:134px">Home</a>
      <a class="is-active" style="left:157px">About</a>
      <a style="left:181px">Vehicles we support</a>
      <a style="left:232px">Link to IOS and Android Apps</a>
      <a style="left:303px">Contact us</a>
    </nav>
    <span class="btn-pill login">LOGIN</span>
  </header>

  <svg class="hero-bg about-hero-bg" viewBox="0 0 405 205" role="img" aria-label="Photo of a team joining hands over a desk with a network line overlay">
    <defs>
      <linearGradient id="aboutHeroFill" x1="0" y1="0" x2="1" y2="1">
        <stop offset="0" stop-color="#2c3f98"/>
        <stop offset="0.55" stop-color="#26347a"/>
        <stop offset="1" stop-color="#161e4e"/>
      </linearGradient>
    </defs>
    <polygon points="0,0 405,0 405,205 0,155" fill="url(#aboutHeroFill)"/>
  </svg>
  <h1 class="hero-title about-title">About</h1>
  <p class="about-lede">Lorem ipsum dolor sit amet, consectetuer adipiscing elit, sed diam nonummy nibh euismod tincidunt ut laoreet dolore magna aliquam erat vol</p>

  <h2 class="section-title who-title">Who We Are?</h2>
  <div class="who-copy">
    <p>Lorem ipsum dolor sit amet, consectetuer adipiscing elit, sed diam nonummy nibh euismod tincidunt ut laoreet dolore magna aliquam erat volutpat. Ut wisi enim ad minim veniam, quis nostrud exerci tation ullamcorper suscipit lobortis nisl ut aliquip ex ea commodo consequat. Duis autem vel eum iriure dolor in hendrerit in vulputate velit esse molestie consequat, vel illum dolore eu feugiat nulla facilisis at vero eros et accumsan et iusto odio dignissim qui blandit praesent luptatum zzril delenit augue duis dolore te feugait nulla facilisi.</p>
    <p>Lorem ipsum dolor sit amet, consectetuer adipiscing elit, sed diam nonummy nibh euismod tincidunt ut laoreet dolore magna aliquam erat volutpat. Ut wisi enim ad minim veniam, quis nostrud exerci tation ullamcorper suscipit lobortis nisl ut aliquip ex ea commodo consequat.</p>
    <p>Lorem ipsum dolor sit amet, consectetuer adipiscing elit, sed diam nonummy nibh euismod tincidunt ut laoreet dolore magna aliquam erat volutpat. Ut wisi enim ad minim veniam, quis nostrud exerci tation ullamcorper suscipit lobortis nisl ut aliquip ex ea commodo consequat. Duis autem vel eum iriure dolor in hendrerit in vulputate velit esse molestie consequat, vel illum dolore eu feugiat nulla facilisis at vero eros et accumsan et iusto odio dignissim qui blandit praesent luptatum zzril delenit augue duis dolore te feugait nulla facilisi.</p>
    <p>Lorem ipsum dolor sit amet, consectetuer adipiscing elit, sed diam nonummy nibh euismod tincidunt ut laoreet dolore magna aliquam erat volutpat. Ut wisi enim ad minim veniam, quis nostrud exerci tation ullamcorper suscipit lobortis nisl ut aliquip ex ea commodo consequat. Duis autem vel eum iriure dolor in hendrerit in vulputate velit esse molestie consequat, vel illum dolore eu feugiat nulla facilisis at vero eros et accumsan et iusto odio dignissim qui blandit praesent luptatum zzril delenit augue duis dolore te feugait nulla facilisi.</p>
  </div>
  <span class="btn-pill read-more">Read More</span>

  <section class="team-band">
    <h2 class="section-title team-title">Our Team</h2>
    <div class="team-card team-card--first" role="img" aria-label="Portrait photo of team member Marlow">
      <span class="member-name">Marlow</span>
      <span class="member-links"><span></span><span></span><span></span></span>
    </div>
    <div class="team-card team-card--second" role="img" aria-label="Portrait photo of a team member in a plaid shirt"></div>
    <div class="team-card team-card--third" role="img" aria-label="Portrait photo of a team member in a denim shirt"></div>
  </section>

  <footer class="site-footer">
    <nav class="footer-nav">
      <a style="left:38px">Home</a>
      <a style="left:61px">About</a>
      <a style="left:85px">Vehicles we support</a>
      <a style="left:137px">Link to IOS and Android Apps</a>
      <a style="left:207px">Contact us</a>
    </nav>
    <span class="email-field">E-Mail Address</span>
    <span class="btn-pill subscribe">Subscribe</span>
  </footer>
  <p class="copyright">Copyright © 2020 Volt Roam Mobile</p>
  <div class="social" aria-label="Social links"><span></span><span></span><span></span><span></span><span></span></div>
</section>

</body>
</html>
```